Redesign Website - Current one too plain

The description is in the uploaded file. Please let me know if you need any more information. I'd prefer it if someone could implement the design to a WordPress site but the best design will win, regardless.
I would like the forms to look nice as well
UPDATE:
I don't think we can use the images that I provided, I think they make the site look a bit 'cheap' and I really don't know how to replace them. One thought I have had is to make the "Simple, Unique, Effective" a second feature on the right side of the page with the search on the left
Target Market(s)
Small companies, private sellers of cars and people who rent their caravan/holiday home out
Industry/Entity Type
Advertising
Number of Pages Required
3 page
Colors
Designer to choose colors to be used in the design.
Look and feel
Each slider illustrates characteristics of the customer's brand and the style your logo design should communicate.

```html
<!DOCTYPE html>
<html lang="en">
<head>
<meta charset="utf-8">
<title>Tagora – Find the advert behind the code</title>
<link href="https://fonts.googleapis.com/css2?family=Poppins:wght@400;500;600;700;800&display=swap" rel="stylesheet">
<style>
:root{
  --lime:#dcfc2c;
  --lime-soft:#e6ff4a;
  --ink:#2c2c2c;
  --ink-deep:#232323;
  --paper:#f4f5f7;
  --white:#ffffff;
  --grey-text:#3a3a3a;
  --star:#f5c518;
}
*{box-sizing:border-box;margin:0;padding:0}
html,body{width:1200px;height:3446px;overflow:hidden}
body{position:relative;font-family:'Poppins',sans-serif;color:var(--ink);background:var(--white)}
.abs{position:absolute}

/* header */
.site-header{left:0;top:0;width:1200px;height:72px;background:var(--ink)}
.brand{display:flex;align-items:center;gap:10px;color:var(--lime);font-weight:500;letter-spacing:4px}
.brand-dot{border-radius:50%;background:var(--lime)}
.site-header .brand{position:absolute;left:115px;top:20px;font-size:22px}
.site-header .brand-dot{width:30px;height:30px}
.main-nav{position:absolute;top:27px;left:0;width:1200px;height:20px}
.main-nav a,.foot-nav a{position:absolute;color:var(--white);text-decoration:none;font-weight:600;font-size:15px;white-space:nowrap}

/* hero */
.hero{left:0;top:72px;width:1200px;height:523px;background:linear-gradient(160deg,var(--lime-soft) 0%,var(--lime) 45%,#b9d81c 100%)}
.hero-photo{left:335px;top:90px;width:865px;height:400px;border-radius:6px 0 0 6px;background:linear-gradient(180deg,rgba(225,225,220,.0) 0%,rgba(190,190,188,.75) 40%,#8d8f8e 100%)}
.plate{left:112px;top:159px;width:319px;height:269px;background:var(--ink);border-radius:18px}
.plate-code{position:absolute;left:0;top:30px;width:100%;display:flex;justify-content:space-around;padding:0 30px;color:var(--lime);font-weight:700;font-size:168px;line-height:1}
.arrow{position:absolute;width:0;height:0;border-left:11px solid transparent;border-right:11px solid transparent}
.arrow.up{border-bottom:11px solid var(--white)}
.arrow.down{border-top:11px solid var(--white)}
.type-btn{top:391px;height:38px;background:var(--white);border:3px solid var(--ink);border-radius:8px;font-weight:600;font-size:15px;color:var(--ink);display:flex;align-items:center;justify-content:center}
.search-btn{left:112px;top:450px;width:118px;height:46px;background:var(--ink);border-radius:9px;color:var(--lime);font-weight:700;font-size:15px;display:flex;align-items:center;justify-content:center;gap:8px}

/* features */
.features{left:0;top:595px;width:1200px;height:478px;background:linear-gradient(115deg,#eceef1 0%,var(--paper) 40%,#fafafb 100%)}
.feature{top:739px;width:234px;height:214px;background:var(--white);border:13px solid var(--lime);border-radius:34px;box-shadow:0 6px 14px rgba(180,210,0,.35);text-align:center;padding-top:72px}
.feature h3{font-size:20px;font-weight:600;color:var(--ink)}
.feature p{font-size:15px;line-height:17px;margin-top:8px;padding:0 20px;color:var(--ink)}
.feature-tab{top:705px;width:116px;height:104px;background:var(--lime);border-radius:12px;display:flex;align-items:center;justify-content:center}

/* about */
.about{left:0;top:1073px;width:1200px;height:586px;background:var(--ink)}
.about-photo{left:0;top:1204px;width:549px;height:295px;border-radius:0 60px 30px 0;background:linear-gradient(180deg,#9a9a98 0%,#d2d2d0 45%,#6e6f6f 100%)}
.about h2{position:absolute;left:603px;top:108px;color:var(--lime);font-size:38px;font-weight:700}
.about p{position:absolute;left:603px;top:174px;width:486px;color:var(--white);font-size:15.5px;line-height:30px;text-align:justify}
.pill-btn{background:var(--lime);color:var(--ink);font-weight:700;font-size:15px;border-radius:9px;display:flex;align-items:center;justify-content:center}
.about .pill-btn{position:absolute;left:603px;top:444px;width:128px;height:46px}

/* testimonials */
.testimonials{left:0;top:1659px;width:1200px;height:723px;background:linear-gradient(110deg,#f0f1f3 0%,#fbfbfc 50%,#eef0f2 100%)}
.testimonial-band{left:0;top:1924px;width:1200px;height:458px;background:var(--lime)}
.testimonials-title{left:112px;top:1770px;font-size:39px;font-weight:700}
.reviewer{left:112px;top:1834px;font-size:15px}
.stars{left:112px;top:1873px;display:flex;gap:5px}
.quote{left:115px;top:1980px;width:486px;font-size:15.5px;line-height:30px;text-align:justify;color:var(--grey-text)}
.view-all{left:113px;top:2264px;font-size:18px;font-weight:700;border-bottom:2px solid var(--ink);padding-bottom:2px}
.photo-frame{left:717px;top:1796px;width:349px;height:479px;background:var(--ink);border-radius:30px}
.portrait{left:730px;top:1806px;width:359px;height:482px;border-radius:24px;background:linear-gradient(180deg,#c9d3d6 0%,#b8c4c7 45%,#27324a 70%,#1e273b 100%)}

/* contact */
.contact{left:0;top:2382px;width:1200px;height:685px;background:linear-gradient(120deg,#eceef0 0%,#fafafa 50%,#f1f2f4 100%)}
.contact-title{left:0;top:2487px;width:1200px;text-align:center;font-size:39px;font-weight:700}
.contact-form{left:268px;top:2572px;width:666px;height:376px;background:var(--ink);border-radius:36px}
.field{left:325px;width:551px;height:73px;background:var(--white);border-radius:22px;font-size:17px;color:var(--grey-text);padding:22px 0 0 26px}
.char-count{left:350px;top:2869px;color:var(--white);font-size:15px}
.submit{left:537px;top:2926px;width:127px;height:44px;font-size:14px}

/* footer */
.site-footer{left:0;top:3067px;width:1200px;height:379px;background:linear-gradient(150deg,#2f2f2f 0%,var(--ink-deep) 60%,#2a2a2a 100%)}
.site-footer .brand{position:absolute;left:0;top:86px;width:1200px;justify-content:center;font-size:52px;letter-spacing:8px;gap:20px}
.site-footer .brand-dot{width:62px;height:62px}
.foot-nav{position:absolute;left:0;top:197px;width:1200px;height:20px}
.socials{position:absolute;left:0;top:258px;width:1200px;display:flex;justify-content:center;gap:33px}
.socials span{width:14px;height:14px;border-radius:50%;background:var(--lime)}
.foot-rule{position:absolute;left:112px;top:322px;width:972px;height:1px;background:#6a6a6a}
.copyright{position:absolute;left:115px;top:339px;color:var(--white);font-size:15px}
</style>
</head>
<body>

<header class="abs site-header">
  <div class="brand"><span class="brand-dot"></span>Tagora</div>
  <nav class="main-nav">
    <a style="left:662px">HOME</a>
    <a style="left:750px">ABOUT US</a>
    <a style="left:863px">TESTIMONIALS</a>
    <a style="left:1010px">CONTACT</a>
  </nav>
</header>

<section class="abs hero"></section>
<div class="abs hero-photo" role="img" aria-label="Photo of a static caravan, a silver SUV and a silver sign-written van with code tags"></div>

<div class="abs plate">
  <span class="arrow up" style="left:213px;top:20px;left:214px"></span>
  <span class="arrow up" style="left:214px;top:20px"></span>
  <span class="arrow up" style="left:92px;top:20px"></span>
  <span class="arrow up" style="left:214px;top:20px;left:343px"></span>
  <div class="plate-code"><span>A</span><span>1</span></div>
  <span class="arrow down" style="left:92px;top:183px"></span>
  <span class="arrow down" style="left:229px;top:183px"></span>
</div>
<div class="abs type-btn" style="left:112px;width:100px">CAR</div>
<div class="abs type-btn" style="left:220px;width:101px">CARAVAN</div>
<div class="abs type-btn" style="left:329px;width:101px">COMPANY</div>
<div class="abs search-btn">SEARCH
  <svg width="20" height="20" viewBox="0 0 20 20" fill="none" stroke="#fff" stroke-width="2"><circle cx="8" cy="8" r="6"/><path d="M12.5 12.5 18 18"/></svg>
</div>

<section class="abs features"></section>
<article class="abs feature" style="left:186px"><h3>SIMPLE</h3><p>create your advert and display your code</p></article>
<article class="abs feature" style="left:477px"><h3>UNIQUE</h3><p>customers find you by an easy-to-remember code</p></article>
<article class="abs feature" style="left:765px"><h3>EFFECTIVE</h3><p>customers are directed to you and not a list of your competitors</p></article>

<div class="abs feature-tab" style="left:245px">
  <svg width="76" height="76" viewBox="0 0 76 76" fill="none" stroke="#222" stroke-width="2.5">
    <circle cx="18" cy="20" r="8"/><circle cx="18" cy="20" r="3"/>
    <circle cx="56" cy="20" r="8"/><circle cx="56" cy="20" r="3"/>
    <circle cx="37" cy="50" r="14"/><path d="M30 50l5 5 9-10"/>
  </svg>
</div>
<div class="abs feature-tab" style="left:536px">
  <svg width="76" height="76" viewBox="0 0 76 76" fill="none" stroke="#222" stroke-width="2.5">
    <circle cx="32" cy="32" r="22"/><circle cx="32" cy="32" r="15"/><circle cx="32" cy="32" r="8"/>
    <path d="M48 48l16 16"/>
  </svg>
</div>
<div class="abs feature-tab" style="left:823px">
  <svg width="76" height="76" viewBox="0 0 76 76" fill="none" stroke="#222" stroke-width="2.5">
    <rect x="10" y="36" width="12" height="28"/>
    <path d="M22 40l12-20v-8h6v22h18v26H22"/>
    <path d="M54 10l2 5 5 2-5 2-2 5-2-5-5-2 5-2z"/>
  </svg>
</div>

<section class="abs about">
  <h2>ABOUT US</h2>
  <p>Lorem ipsum dolor sit amet, consectetur adipiscing elit, sed do eiusmod tempor incididunt ut labore et dolore magna aliqua. Ut enim ad minim veniam, quis nostrud exercitation ullamco laboris nisi ut aliquip ex ea commodo consequat. Duis aute irure dolor in reprehenderit in voluptate velit esse cillum dolore eu fugiat nulla pariatur. Excepteur sint occaecat cupidatat non proident, sunt in culpa qui officia deserunt mollit anim id est laborum.</p>
  <div class="pill-btn">READ MORE</div>
</section>
<div class="abs about-photo" role="img" aria-label="Photo of a silver SUV with a code tag on the rear window"></div>

<section class="abs testimonials"></section>
<div class="abs testimonial-band"></div>
<h2 class="abs testimonials-title">TESTIMONIALS</h2>
<p class="abs reviewer">-Dana R</p>
<div class="abs stars">
  <svg width="20" height="19" viewBox="0 0 24 23"><path fill="#f5c518" d="M12 0l3.6 7.4 8.1 1.2-5.9 5.7 1.4 8.1L12 18.6l-7.2 3.8 1.4-8.1L.3 8.6l8.1-1.2z"/></svg>
  <svg width="20" height="19" viewBox="0 0 24 23"><path fill="#f5c518" d="M12 0l3.6 7.4 8.1 1.2-5.9 5.7 1.4 8.1L12 18.6l-7.2 3.8 1.4-8.1L.3 8.6l8.1-1.2z"/></svg>
  <svg width="20" height="19" viewBox="0 0 24 23"><path fill="#f5c518" d="M12 0l3.6 7.4 8.1 1.2-5.9 5.7 1.4 8.1L12 18.6l-7.2 3.8 1.4-8.1L.3 8.6l8.1-1.2z"/></svg>
  <svg width="20" height="19" viewBox="0 0 24 23"><path fill="#f5c518" d="M12 0l3.6 7.4 8.1 1.2-5.9 5.7 1.4 8.1L12 18.6l-7.2 3.8 1.4-8.1L.3 8.6l8.1-1.2z"/></svg>
  <svg width="20" height="19" viewBox="0 0 24 23"><path fill="#f5c518" d="M12 0l3.6 7.4 8.1 1.2-5.9 5.7 1.4 8.1L12 18.6l-7.2 3.8 1.4-8.1L.3 8.6l8.1-1.2z"/></svg>
</div>
<p class="abs quote">Lorem ipsum dolor sit amet, consectetur adipiscing elit, sed do eiusmod tempor incididunt ut labore et dolore magna aliqua. Ut enim ad minim veniam, quis nostrud exercitation ullamco laboris nisi ut aliquip ex ea commodo consequat. Duis aute irure dolor in reprehenderit in voluptate velit esse cillum dolore eu fugiat nulla pariatur. Excepteur sint occaecat cupidatat non proident, sunt in culpa qui officia deserunt mollit anim id est laborum.</p>
<div class="abs view-all">VIEW ALL</div>
<div class="abs photo-frame"></div>
<div class="abs portrait" role="img" aria-label="Portrait photo of the reviewer in a dark suit with arms folded"></div>

<section class="abs contact"></section>
<h2 class="abs contact-title">CONTACT US</h2>
<form class="abs contact-form" aria-label="Contact form"></form>
<div class="abs field" style="top:2607px">Name*</div>
<div class="abs field" style="top:2697px">Email*</div>
<div class="abs field" style="top:2789px">Message*</div>
<p class="abs char-count">0 of 1000 max characters</p>
<div class="abs pill-btn submit">SUBMIT</div>

<footer class="abs site-footer">
  <div class="brand"><span class="brand-dot"></span>Tagora</div>
  <nav class="foot-nav">
    <a style="left:386px">HOME</a>
    <a style="left:475px">ABOUT US</a>
    <a style="left:588px">TESTIMONIALS</a>
    <a style="left:735px">CONTACT</a>
  </nav>
  <div class="socials" aria-label="Social links">
    <span></span><span></span><span></span><span></span><span></span>
  </div>
  <div class="foot-rule"></div>
  <p class="copyright">© 2023 &nbsp;tagora</p>
</footer>

</body>
</html>
```